Looking for a dynamic business card for a pizzeria.

A business card with our food, logo, and space for name, title, email, website, phone. The card should convey quality, unique, amazing. On the front, I envision food photo or photos with the owners names and contact information. On the back, more food with locations, website, facebook, twitter, instagram icons. It should look polished, not cartoonish, or plain.
Target Market(s)
upscale, local food buyers, 30-50 years in age.
Industry/Entity Type
Restaurant
Contact Information for Business Card
Business Name: Bru'nettix, LLC
Website: www.brunettix.com
Back:
2 locations: (can list on the back of card)
1. Marlow Point
4087 Corlan Avenue
Harlow Bay, WA 98531
360-481-5067
2. Cedar Knoll
7315 Wendmere Road
Harlow Bay, WA 98534
360-293-8840
front:
EDITABLE space for
Business name
Person's Name
title
2nd title
Email address
cell-phone number
Requirements
Must have
- logo
- my food photo or photos (no watermarks showing)
- locations on back
- Person contact information on front
- full bleed

```html
<!DOCTYPE html>
<html lang="en">
<head>
<meta charset="utf-8">
<title>Bru'nettix Business Card</title>
<link href="https://fonts.googleapis.com/css2?family=Oswald:wght@500;700&family=Questrial&display=swap" rel="stylesheet">
<style>
  :root {
    --green: #1f5a2c;
    --red: #b3191d;
    --cream: #fbefd8;
    --cream-stripe: #f4e2c2;
    --white: #ffffff;
    --stage: #e9e6e0;
  }
  * { margin: 0; padding: 0; box-sizing: border-box; }
  html, body { width: 1200px; height: 843px; overflow: hidden; }
  body {
    background: var(--stage);
    position: relative;
    font-family: "Questrial", sans-serif;
  }
  .card {
    position: absolute;
    width: 640px;
    height: 366px;
    overflow: hidden;
    box-shadow: 0 6px 18px rgba(0,0,0,0.18);
  }

  /* Back of card */
  .card-back {
    left: 480px; top: 40px;
    background: var(--green);
    color: var(--white);
  }
  .back-brand {
    position: absolute;
    top: 72px; left: 280px;
    display: flex; align-items: center; gap: 14px;
  }
  .brand-dot {
    display: block;
    border-radius: 50%;
  }
  .back-brand .brand-dot { width: 34px; height: 34px; background: var(--white); }
  .back-brand .brand-name {
    font-family: "Oswald", sans-serif;
    font-weight: 500;
    font-size: 40px;
    letter-spacing: 1px;
    line-height: 1;
  }
  .social {
    position: absolute; top: 160px; right: 32px;
    display: flex; gap: 10px;
  }
  .social span {
    width: 16px; height: 16px; border-radius: 50%;
    background: var(--white);
  }
  .divider {
    position: absolute; left: 30px; right: 30px; top: 210px;
    height: 1px; background: var(--white);
  }
  .location {
    position: absolute;
    font-style: normal;
    font-size: 17px; line-height: 1.3;
  }
  .location .area { font-size: 15px; }
  .location .phone {
    font-family: "Oswald", sans-serif; font-weight: 500;
    font-size: 17px; letter-spacing: 0.5px;
  }
  .location-one { left: 40px; top: 92px; }
  .location-two { right: 40px; top: 226px; text-align: right; }

  /* Front of card */
  .card-front {
    left: 80px; top: 437px;
    background: repeating-linear-gradient(90deg, var(--cream) 0 22px, var(--cream-stripe) 22px 44px);
  }
  .front-wave { position: absolute; left: 0; top: 0; width: 640px; height: 366px; }
  .person { position: absolute; left: 36px; top: 28px; }
  .person-name {
    font-family: "Oswald", sans-serif; font-weight: 700;
    font-size: 24px; line-height: 1.2; color: var(--green); letter-spacing: 0.5px;
  }
  .person-title {
    font-family: "Oswald", sans-serif; font-weight: 700;
    font-size: 18px; line-height: 1.2; color: var(--red); letter-spacing: 0.5px;
  }
  .front-brand {
    position: absolute; left: 36px; top: 108px;
    display: flex; align-items: center; gap: 16px;
  }
  .front-brand .brand-name {
    font-family: "Oswald", sans-serif; font-weight: 500;
    font-size: 62px; line-height: 1; color: var(--green); letter-spacing: 1px;
  }
  .front-brand .brand-dot { width: 70px; height: 70px; background: var(--red); }
  .contact {
    position: absolute; right: 30px; bottom: 20px;
    list-style: none; color: var(--white);
    font-size: 19px; line-height: 1.45;
  }
  .contact li { display: flex; justify-content: flex-end; align-items: center; gap: 10px; }
  .contact svg { width: 16px; height: 16px; flex: none; }
</style>
</head>
<body>

<section class="card card-back" aria-label="Card back">
  <div class="back-brand">
    <span class="brand-dot"></span>
    <span class="brand-name">BRU'NETTIX</span>
  </div>
  <address class="location location-one">
    <div class="area">Marlow Point</div>
    <div>4087 Corlan Avenue</div>
    <div>Harlow Bay, WA 98531</div>
    <div class="phone">P : 360-481-5067</div>
  </address>
  <div class="social" aria-label="Social links">
    <span></span><span></span>
  </div>
  <div class="divider"></div>
  <address class="location location-two">
    <div class="area">Cedar Knoll</div>
    <div>7315 Wendmere Road</div>
    <div>Harlow Bay, WA 98534</div>
    <div class="phone">P : 360-293-8840</div>
  </address>
</section>

<section class="card card-front" aria-label="Card front">
  <svg class="front-wave" viewBox="0 0 640 366" aria-hidden="true">
    <path d="M0 222 C 140 262, 320 268, 640 262 L640 366 L0 366 Z" fill="var(--green)"/>
    <path d="M0 214 C 150 252, 330 258, 640 252" fill="none" stroke="var(--red)" stroke-width="5"/>
  </svg>
  <div class="person">
    <div class="person-name">MARCO BELLINI</div>
    <div class="person-title">FOUNDER</div>
  </div>
  <div class="front-brand">
    <span class="brand-name">BRU'NETTIX</span>
    <span class="brand-dot"></span>
  </div>
  <ul class="contact">
    <li>555 512 7046
      <svg viewBox="0 0 16 16"><rect x="4" y="1" width="8" height="14" rx="1.5" fill="none" stroke="#fff" stroke-width="1.5"/><circle cx="8" cy="12.5" r="0.9" fill="#fff"/></svg>
    </li>
    <li>name@brunettix.com
      <svg viewBox="0 0 16 16"><rect x="1" y="3.5" width="14" height="9" fill="none" stroke="#fff" stroke-width="1.5"/><path d="M1 3.5 L8 9 L15 3.5" fill="none" stroke="#fff" stroke-width="1.5"/></svg>
    </li>
    <li>www.brunettix.com
      <svg viewBox="0 0 16 16"><circle cx="8" cy="8" r="6.5" fill="none" stroke="#fff" stroke-width="1.5"/><ellipse cx="8" cy="8" rx="2.8" ry="6.5" fill="none" stroke="#fff" stroke-width="1.2"/><line x1="1.5" y1="8" x2="14.5" y2="8" stroke="#fff" stroke-width="1.2"/></svg>
    </li>
  </ul>
</section>

</body>
</html>
```